Marlith Construction Core Values Wall Design

Core Values Wall Design for our Wall, I’m not exactly sure visually what we would want it to look like. Maybe some acrylic stand offs that could go on brick? If that’s a possibility. That’s where we have the most space in the office. But we could do other locations too.

These are our core values
• Safety
• Integrity
• Quality
• Client-Focused Solutions
• Continuous Improvement
• Positive Culture and Stewardship

Our vision/mission statement is Craft Assured.

```html
<!DOCTYPE html>
<html lang="en">
<head>
<meta charset="UTF-8">
<title>Marlith Construction – Core Values Wall Panel: Safety</title>
<link rel="stylesheet" href="https://fonts.googleapis.com/css2?family=Montserrat:wght@700;800;900&display=swap">
<style>
  :root {
    --backdrop: #e9e7e5;
    --acrylic: #f3f1f0;
    --acrylic-edge: #dcd8d6;
    --standoff: #b9bbbe;
    --standoff-shine: #eef0f2;
    --tile-slate: #819faf;
    --band-black: #0a0f12;
    --icon-white: #ffffff;
    --brand-blue: #1b5fa6;
    --brand-red: #e0323c;
  }
  * { box-sizing: border-box; margin: 0; padding: 0; }
  html, body {
    width: 1200px;
    height: 800px;
    overflow: hidden;
    background: var(--backdrop);
    font-family: "Montserrat", Arial, sans-serif;
  }
  .canvas {
    position: relative;
    width: 1200px;
    height: 800px;
  }
  .value-panel {
    position: absolute;
    left: 60px;
    top: 40px;
    width: 1080px;
    height: 720px;
    background: linear-gradient(135deg, #f7f6f5 0%, var(--acrylic) 55%, #ebe8e6 100%);
    border: 2px solid var(--acrylic-edge);
    border-radius: 4px;
    box-shadow: 0 18px 40px rgba(0,0,0,0.12);
  }
  .standoff {
    position: absolute;
    width: 46px;
    height: 46px;
    border-radius: 50%;
    background: radial-gradient(circle at 35% 35%, var(--standoff-shine) 0%, var(--standoff) 55%, #8e9195 100%);
  }
  .standoff--tl { left: 70px; top: 50px; }
  .standoff--tr { right: 30px; top: 210px; }
  .standoff--bl { left: 70px; bottom: 70px; }
  .standoff--br { right: 30px; bottom: 40px; }

  .value-tile {
    position: absolute;
    left: 173px;
    top: 110px;
    width: 475px;
    height: 510px;
    background: var(--tile-slate);
    border-radius: 0 16px 0 0;
    overflow: hidden;
  }
  .value-tile__icon {
    position: absolute;
    left: 50%;
    top: 52px;
    width: 290px;
    height: 330px;
    transform: translateX(-50%);
  }
  .value-tile__band {
    position: absolute;
    left: 0;
    bottom: 0;
    width: 100%;
    height: 120px;
    background: var(--band-black);
    display: flex;
    align-items: center;
    justify-content: center;
  }
  .value-tile__label {
    color: var(--icon-white);
    font-weight: 900;
    font-size: 62px;
    letter-spacing: 1px;
  }

  .panel-divider {
    position: absolute;
    left: 700px;
    top: 290px;
    width: 3px;
    height: 290px;
    background: var(--brand-blue);
  }

  .brand-block {
    position: absolute;
    left: 730px;
    top: 330px;
    width: 320px;
    text-align: center;
  }
  .brand-block__name {
    color: var(--brand-blue);
    font-weight: 800;
    font-size: 54px;
    line-height: 1;
    letter-spacing: 1px;
  }
  .brand-block__name-sub {
    display: block;
    margin-top: 10px;
    font-size: 17px;
    letter-spacing: 7px;
  }
  .brand-block__tagline {
    margin-top: 34px;
    color: var(--brand-red);
    font-weight: 800;
    font-size: 22px;
    letter-spacing: 2px;
    text-transform: uppercase;
  }
</style>
</head>
<body>
  <main class="canvas">
    <section class="value-panel" aria-label="Core value panel: Safety">
      <span class="standoff standoff--tl"></span>
      <span class="standoff standoff--tr"></span>
      <span class="standoff standoff--bl"></span>
      <span class="standoff standoff--br"></span>

      <div class="value-tile">
        <svg class="value-tile__icon" viewBox="0 0 290 330" aria-hidden="true">
          <path d="M145 12 C110 42 65 52 18 50 L18 160 C18 235 70 290 145 318 C220 290 272 235 272 160 L272 88 C225 92 180 60 145 12 Z"
                fill="none" stroke="var(--icon-white)" stroke-width="22" stroke-linejoin="round"/>
          <path d="M98 178 L142 222 L210 160" fill="none" stroke="var(--icon-white)"
                stroke-width="22" stroke-linecap="round" stroke-linejoin="round"/>
        </svg>
        <div class="value-tile__band">
          <h1 class="value-tile__label">SAFETY</h1>
        </div>
      </div>

      <div class="panel-divider"></div>

      <div class="brand-block">
        <p class="brand-block__name">Marlith<span class="brand-block__name-sub">CONSTRUCTION</span></p>
        <p class="brand-block__tagline">Craft Assured</p>
      </div>
    </section>
  </main>
</body>
</html>
```